NCCS Brochure Design

Northfield Council of Clinical Standards (NCCS) needs a whole new brochure. I've upload EPS logos and past brochures. Our tagline is to "modernize healthcare" and we think our brochure should reflect that, so that's the purpose of this project.

NCCS is a proven leader in healthcare education, training and
consulting services for health professionals. We’ve earned a reputation for excellence in healthcare quality improvement and management.

NCCS works to improve healthcare quality by educating healthcare professionals about healthcare best practices. We focus on instructing our clients on how to plan for, measure, and improve healthcare quality in all facilities and facets such as:

Patient Safety
Infection Control
Performance Improvement
Risk Management
Compliance and Accreditation
Health and Hospital Administration
Health Insurance
Healthcare Financial Management
Facility Management and Safety

DESIGN SUGGESTIONS:

Brochure Size: 8.5 X 11 full size brochure or 8.5 X 11 trifold brochure

Number of Pages: 2 to 3

Colors: Feel free to use a wide array of colors but try to stay away from colors that are too loud, ex: Pink, Purple, Neon Green.

Themes: Professional, Educational

Designs:

Pelvor by Tobin Haskell

Lumora Leaflet by Derek Molloy

Gears of assembly by Vostrelle

Figura de Mr KB by qzpt

http://www.plimvaro.com/post/28461937520/10-creative-brochure-designs

Don't limit yourself to these examples. However, these are examples we liked

Reason: We would like to see more designs

We want more full page designs than tri-fold 

We are considering both tri-fold and full-page but would like to see more full page designs 

Reason: Our lead designer making the decisions on this project has been fired. I apologize for the inconvenience. We want extend the project one last time

Target Market(s)

Students, Doctors, and Educational Professionals

Industry/Entity Type

Healthcare

Font styles to use
Serif
Sans Serif
Decorative
Script

Requirements
Should not have
• Pink, Purple, Neon Green colors

```html
<!DOCTYPE html>
<html lang="en">
<head>
<meta charset="utf-8">
<title>NCCS Trifold Brochure</title>
<link href="https://fonts.googleapis.com/css2?family=Roboto+Condensed:ital,wght@0,400;0,700;1,400;1,700&display=swap" rel="stylesheet">
<style>
  :root {
    --page-bg: #d9d9d4;
    --paper: #ffffff;
    --paper-shade: #f1f2f4;
    --navy: #2b2f6b;
    --body-text: #5a5d66;
    --band-blue: #4fa6dc;
    --band-light: #6cbce8;
    --panel-blue-top: #4b9fe0;
    --panel-blue-bottom: #2f7cc6;
    --title-grey: #e4e6e8;
    --white: #ffffff;
  }
  * { box-sizing: border-box; margin: 0; padding: 0; }
  html, body {
    width: 1200px; height: 803px; overflow: hidden;
    background: var(--page-bg);
    font-family: "Roboto Condensed", Arial, sans-serif;
  }
  .brochure {
    position: absolute; left: 60px; top: 40px;
    width: 1080px; height: 723px;
    display: flex;
    box-shadow: 0 6px 24px rgba(0,0,0,.18);
  }
  .panel { position: relative; width: 360px; height: 100%; overflow: hidden; }
  .panel--intro { background: linear-gradient(180deg, var(--paper) 40%, var(--paper-shade)); }
  .panel--feature { background: var(--paper); border-left: 1px solid #e3e4e7; }
  .panel--about {
    background: linear-gradient(180deg, var(--panel-blue-top), var(--panel-blue-bottom));
    color: var(--white);
  }
  .photo { position: absolute; }
  .photo--doctor {
    left: 0; top: 0; width: 360px; height: 270px;
    background: linear-gradient(100deg, #cfd3d8 0%, #f3f3f1 45%, #e6e9ec 100%);
  }
  .photo--lobby {
    left: 0; top: 0; width: 360px; height: 270px;
    background: linear-gradient(90deg, #e9ebec 0%, #f7f8f8 50%, #dfe3e6 100%);
  }
  .photo--lab {
    left: 32px; top: 360px; width: 296px; height: 190px;
    background: linear-gradient(135deg, #e8eef3 0%, #ffffff 50%, #cfd8e0 100%);
  }
  .title-band {
    position: absolute; left: 0; top: 270px;
    width: 720px; height: 78px;
    display: flex; z-index: 2;
  }
  .title-band__left { width: 360px; background: var(--band-blue); }
  .title-band__right { width: 360px; background: var(--band-light); }
  .title-band__text {
    position: absolute; left: 22px; top: 18px;
    font-weight: 700; font-size: 38px; letter-spacing: -0.5px;
    color: var(--title-grey);
    text-shadow: 1px 2px 2px rgba(0,0,0,.45);
    white-space: nowrap;
  }
  .intro-copy { position: absolute; left: 26px; top: 366px; right: 24px; }
  .heading-navy { color: var(--navy); font-weight: 700; font-size: 14px; margin-bottom: 5px; }
  .body-copy { color: var(--body-text); font-size: 10px; line-height: 1.45; }
  .service-list { list-style: none; margin-bottom: 10px; }
  .service-list li { color: var(--body-text); font-size: 10px; line-height: 1.45; display: flex; gap: 6px; align-items: flex-start; }
  .service-list svg { flex: none; margin-top: 3px; }
  .section-gap { margin-top: 12px; }
  .membership-note { color: var(--navy); font-style: italic; font-weight: 700; font-size: 10px; margin-top: 8px; }
  .web-address { color: var(--navy); font-size: 13px; margin-top: 8px; }
  .feature-copy { position: absolute; left: 32px; right: 30px; top: 566px; }
  .brand { position: absolute; left: 26px; top: 22px; right: 26px; }
  .brand__row { display: flex; align-items: center; gap: 10px; }
  .brand__mark { width: 24px; height: 24px; border-radius: 50%; background: var(--white); }
  .brand__name { font-weight: 700; font-size: 26px; color: var(--white); }
  .brand__full { font-size: 13px; margin-top: 2px; padding-bottom: 7px; border-bottom: 1px solid rgba(255,255,255,.8); }
  .about { position: absolute; left: 26px; right: 24px; top: 104px; }
  .about__title { font-weight: 700; font-size: 22px; margin-bottom: 8px; }
  .about__sub { font-weight: 700; font-style: italic; font-size: 14px; margin-bottom: 3px; }
  .about__copy { font-size: 10px; line-height: 1.45; color: rgba(255,255,255,.92); margin-bottom: 10px; }
  .services__title { font-weight: 700; font-size: 22px; margin: 8px 0 4px; }
  .services__copy { font-size: 12px; line-height: 1.35; margin-bottom: 10px; }
  .facet-list { list-style: none; font-size: 12px; line-height: 1.3; }
  .call-box {
    position: absolute; left: 120px; bottom: 20px;
    width: 214px; height: 64px;
    border: 1px dashed rgba(255,255,255,.8);
    background: var(--panel-blue-bottom);
    box-shadow: 0 6px 10px rgba(0,0,0,.35);
    text-align: center; padding-top: 6px;
  }
  .call-box__label { font-size: 18px; line-height: 1.2; }
  .call-box__phone { font-size: 22px; font-weight: 700; line-height: 1.2; }
</style>
</head>
<body>
<main class="brochure">
  <section class="panel panel--intro">
    <div class="photo photo--doctor" role="img" aria-label="Photo of a smiling doctor in a white coat with a stethoscope"></div>
    <div class="intro-copy">
      <h2 class="heading-navy">Northfield Council of Clinical Standards</h2>
      <p class="body-copy">Led by highly credentialed healthcare professionals, NCCS consultants are uniquely qualified to provide the training and services you seek. Please learn more about us and our services and don't hesitate to use them. Start the transformative process today that will guide you and your team further up the path to excellence.</p>
      <h3 class="heading-navy section-gap">Our Services</h3>
      <ul class="service-list">
        <li><svg width="8" height="8" viewBox="0 0 10 10"><polygon points="5,0 6.2,3.6 10,3.6 7,5.9 8.1,9.6 5,7.4 1.9,9.6 3,5.9 0,3.6 3.8,3.6" fill="#2b2f6b"/></svg>Training and Professional Development in healthcare quality and management subjects</li>
        <li><svg width="8" height="8" viewBox="0 0 10 10"><polygon points="5,0 6.2,3.6 10,3.6 7,5.9 8.1,9.6 5,7.4 1.9,9.6 3,5.9 0,3.6 3.8,3.6" fill="#2b2f6b"/></svg>Workshops and seminars for larger groups</li>
        <li><svg width="8" height="8" viewBox="0 0 10 10"><polygon points="5,0 6.2,3.6 10,3.6 7,5.9 8.1,9.6 5,7.4 1.9,9.6 3,5.9 0,3.6 3.8,3.6" fill="#2b2f6b"/></svg>Consulting services and custom professional development solutions</li>
      </ul>
      <h3 class="heading-navy">NCCS News &amp; Updates</h3>
      <p class="body-copy">NCCS has launched a new website! Take a look around. We still offer all the same products and services, but our website now has some new features. Be sure to check out the members section and apply to be a member today!</p>
      <p class="membership-note">Find out which type of membership is right for you!</p>
      <p class="web-address">www.nccsonline.com</p>
    </div>
  </section>

  <section class="panel panel--feature">
    <div class="photo photo--lobby" role="img" aria-label="Photo of a bright hospital lobby with tall windows"></div>
    <div class="photo photo--lab" role="img" aria-label="Photo of a lab researcher looking into a microscope"></div>
    <p class="feature-copy body-copy">Patient satisfaction and safety in the healthcare field is becoming increasingly important around the world. Hospitals and various health providers are taking great efforts to enforce an environment where healthcare individuals, including doctors, technicians, nurses, etc. are all able to openly and effectively communicate with each other. With so many different areas of the field</p>
  </section>

  <section class="panel panel--about">
    <header class="brand">
      <div class="brand__row">
        <span class="brand__mark"></span>
        <span class="brand__name">NCCS</span>
      </div>
      <p class="brand__full">Northfield Council of Clinical Standards</p>
    </header>
    <div class="about">
      <h2 class="about__title">ABOUT US</h2>
      <h3 class="about__sub">OUR VISION</h3>
      <p class="about__copy">Here at the Northfield Council of Clinical Standards, we believe that the highest quality in healthcare comes from the highest quality people. We envision a care environment that is focused on quality, enabled by healthcare professionals who have been well trained to improve healthcare outcomes, and who are as passionate as we are about improving the delivery of healthcare and the performance of organizations.</p>
      <h3 class="about__sub">Our Mission</h3>
      <p class="about__copy">Our mission is to enhance quality in healthcare by transforming the professionals who work in healthcare. We aim to give you the tools and knowledge that you need to impact healthcare delivery and outcomes and to be an advocate for quality and patient safety.</p>
      <h2 class="services__title">SERVICES</h2>
      <p class="services__copy">NCCS works to improve healthcare quality by educating healthcare professionals about healthcare best practices. We focus on instructing our clients on how to plan for, measure, and improve healthcare quality in all facilities and facets such as:</p>
      <ul class="facet-list">
        <li>Patient Safety</li>
        <li>Infection Control</li>
        <li>Performance Improvement</li>
        <li>Risk Management</li>
        <li>Compliance and Accreditation</li>
        <li>Health and Hospital Administration</li>
        <li>Health Insurance</li>
        <li>Healthcare Financial Management</li>
        <li>Facility Management and Safety</li>
      </ul>
    </div>
    <div class="call-box">
      <p class="call-box__label">CALL NOW</p>
      <p class="call-box__phone">(555) 318-4470</p>
    </div>
  </section>

  <div class="title-band">
    <div class="title-band__left"></div>
    <div class="title-band__right"></div>
    <h1 class="title-band__text">10 Ways to Improve Communication</h1>
  </div>
</main>
</body>
</html>
```